The Truths About Child Neglect

The goal of this info-graphic is to visually command the attention of our intended audience (teen/adult parents, teachers, youth program coordinators, etc.). Because this project has to do with children, the design should have pops of color; it should be an info-graphic that schools and non profit youth organizations would gladly welcome as an addition to their website. It is important though that the aesthetic, while stimulating the viewer, doesn't overpower the information. The final design should ultimately highlight the innocence of childhood.

Note: the information that has been uploaded is currently formatted in a mock-up info-graphic. Please do not follow that aesthetic; the above description is the route that we would like to take things.

Target Market(s)

Parents
Teachers
Youth Organizations
Parent Bloggers

Industry/Entity Type

Childcare

Font styles to use
Serif
Decorative

Colors

Designer to choose colors to be used in the design.

Requirements
Must have
• Visually captivating imagery
• The info-graphic should grab the viewers attention.
• Sources must be sited at the bottom in small print.
• Looks professional
Nice to have
• A story telling flow of imagery within the info-graphic, which makes it easier for viewers to follow the poignant details.
Should not have
• Boring imagery.
• Heavy text/too much wording.
• Lack of sited sources.

```html
<!DOCTYPE html>
<html lang="en">
<head>
<meta charset="utf-8">
<title>The Truths About Child Neglect</title>
<link href="https://fonts.googleapis.com/css2?family=Fredoka:wght@500;600&family=Roboto+Condensed:wght@400;700&display=swap" rel="stylesheet">
<style>
  :root {
    --teal: #2f6f70;
    --mustard: #e0a236;
    --purple: #8b4c8c;
    --purple-dark: #7a4079;
    --paper: #efebe4;
    --ink: #2e2e2e;
    --white: #ffffff;
    --accent-red: #d9534f;
    --frame: #2d5a55;
    --mat: #f2f2ee;
    --sky: #bfe3e2;
  }
  * { box-sizing: border-box; margin: 0; padding: 0; }
  html, body { width: 1200px; height: 2704px; overflow: hidden; }
  body { position: relative; font-family: "Roboto Condensed", sans-serif; color: var(--ink); background: var(--purple); }
  .abs { position: absolute; }

  .hero { left: 0; top: 0; width: 1200px; height: 440px; background: var(--teal); }
  .hero-title { left: 0; top: 90px; width: 1200px; text-align: center; font-family: "Fredoka", sans-serif; font-weight: 600; font-size: 84px; line-height: 96px; color: var(--white); }

  .consequences { left: 0; top: 420px; width: 1200px; height: 1000px; background: var(--mustard); }
  .wave { left: 0; width: 1200px; height: 60px; }

  .label { left: 50%; transform: translateX(-50%); background: var(--white); border: 5px solid var(--accent-red); border-radius: 10px; padding: 14px 46px; text-align: center; font-family: "Fredoka", sans-serif; font-weight: 500; font-size: 40px; line-height: 46px; color: var(--ink); white-space: nowrap; }
  .label-ways { border-color: var(--purple-dark); }

  .note { background: var(--paper); border-radius: 4px; box-shadow: 0 6px 0 rgba(0,0,0,.12); }
  .note::before { content: ""; position: absolute; left: 20px; right: 20px; top: -10px; height: 20px;
    background: radial-gradient(circle, var(--ink) 5px, transparent 6px) 0 0 / 28px 20px repeat-x; }
  .num { width: 44px; height: 44px; border-radius: 50%; background: var(--ink); color: var(--white); font-weight: 700; font-size: 24px; line-height: 44px; text-align: center; }
  .item { text-align: center; }
  .item .num { margin: 0 auto 14px; }
  .item-text { font-size: 24px; line-height: 30px; text-transform: uppercase; color: var(--ink); }
  .icon { margin: 18px auto 0; border-radius: 12px; }

  .ways { left: 0; top: 1420px; width: 1200px; height: 1284px; background: var(--purple); }
  .frame { border: 18px solid var(--frame); background: var(--mat); padding: 22px; }
  .frame .picture { width: 100%; height: 100%; }
  .hanger { width: 120px; height: 70px; }
  .way { color: var(--white); }
  .way-num { font-family: "Fredoka", sans-serif; font-weight: 600; font-size: 72px; line-height: 72px; }
  .way-text { font-size: 24px; line-height: 30px; text-transform: uppercase; }
</style>
</head>
<body>

<header class="abs hero">
  <h1 class="abs hero-title">The Truths<br>About<br>Child Neglect</h1>
</header>

<section class="abs consequences">
  <svg class="abs wave" style="top:-30px" viewBox="0 0 1200 60" preserveAspectRatio="none" aria-hidden="true">
    <path d="M0 30 Q50 0 100 30 T200 30 T300 30 T400 30 T500 30 T600 30 T700 30 T800 30 T900 30 T1000 30 T1100 30 T1200 30 V60 H0Z" fill="var(--mustard)"/>
  </svg>
  <h2 class="abs label" style="top:80px">7 Consequences of<br>A Child Neglect Charge</h2>

  <article class="abs note" style="left:48px;top:230px;width:360px;height:330px">
    <div class="abs item" style="left:20px;top:30px;width:320px">
      <div class="num">1</div>
      <p class="item-text">Jail time</p>
      <div class="icon" role="img" aria-label="Prisoner in striped uniform" style="width:110px;height:130px;background:linear-gradient(#f0b48a,#e07a4f)"></div>
    </div>
  </article>

  <article class="abs note" style="left:430px;top:230px;width:370px;height:330px">
    <div class="abs item" style="left:20px;top:30px;width:330px">
      <div class="num">2</div>
      <p class="item-text">The loss of custody<br>or parental rights</p>
      <div class="icon" role="img" aria-label="Parents and child figures" style="width:170px;height:110px;background:linear-gradient(#e9c07a,#8fb8b0)"></div>
    </div>
  </article>

  <article class="abs note" style="left:832px;top:230px;width:330px;height:680px">
    <div class="abs item" style="left:15px;top:30px;width:300px">
      <div class="num">3</div>
      <p class="item-text">Fines</p>
      <div class="icon" role="img" aria-label="Stack of banknotes" style="width:110px;height:80px;background:linear-gradient(#6fbf73,#3f8f48)"></div>
    </div>
    <div class="abs item" style="left:15px;top:240px;width:300px">
      <div class="num">5</div>
      <p class="item-text">An injunction</p>
      <div class="icon" role="img" aria-label="Legal document" style="width:80px;height:90px;background:linear-gradient(#ffffff,#d8d8d8)"></div>
    </div>
    <div class="abs item" style="left:15px;top:460px;width:300px">
      <div class="num">4</div>
      <p class="item-text">Registration as<br>a sex offender</p>
      <div class="icon" role="img" aria-label="Gender symbols and handcuffs" style="width:150px;height:60px;background:linear-gradient(90deg,#e58fb0,#7fb0d9)"></div>
    </div>
  </article>

  <article class="abs note" style="left:48px;top:580px;width:360px;height:330px">
    <div class="abs item" style="left:20px;top:30px;width:320px">
      <div class="num">6</div>
      <p class="item-text">Involuntary commitment<br>to a mental institution</p>
      <div class="icon" role="img" aria-label="Theatre masks" style="width:140px;height:100px;background:linear-gradient(90deg,#5a7fd0,#d0504f)"></div>
    </div>
  </article>

  <article class="abs note" style="left:472px;top:580px;width:330px;height:330px">
    <div class="abs item" style="left:15px;top:30px;width:300px">
      <div class="num">7</div>
      <p class="item-text">Restrictions on<br>probation and parole</p>
      <svg class="icon" width="130" height="80" viewBox="0 0 130 80" aria-hidden="true" style="display:block">
        <path d="M5 40 Q65 -10 125 40 Q65 90 5 40Z" fill="var(--white)" stroke="var(--ink)" stroke-width="6"/>
        <circle cx="65" cy="40" r="18" fill="var(--ink)"/>
      </svg>
    </div>
  </article>

  <div class="abs" role="img" aria-label="Potted cactus and coffee mug" style="left:700px;top:860px;width:200px;height:120px;border-radius:14px;background:linear-gradient(90deg,#6aa86c,#3e7f7c)"></div>
</section>

<section class="abs ways">
  <svg class="abs wave" style="top:-30px" viewBox="0 0 1200 60" preserveAspectRatio="none" aria-hidden="true">
    <path d="M0 30 Q50 0 100 30 T200 30 T300 30 T400 30 T500 30 T600 30 T700 30 T800 30 T900 30 T1000 30 T1100 30 T1200 30 V60 H0Z" fill="var(--purple)"/>
  </svg>
  <h2 class="abs label label-ways" style="top:50px">8 Ways You Can Be<br>Charged With Child Neglect</h2>

  <svg class="abs hanger" style="left:256px;top:150px" viewBox="0 0 120 70" aria-hidden="true"><path d="M0 70 L60 4 L120 70" fill="none" stroke="var(--ink)" stroke-width="4"/><circle cx="60" cy="6" r="6" fill="var(--ink)"/></svg>
  <div class="abs frame" style="left:176px;top:220px;width:280px;height:320px"><div class="picture" role="img" aria-label="Child playing outside by a tree on a hill" style="background:linear-gradient(var(--sky) 55%,#7cc26b 55%)"></div></div>

  <svg class="abs hanger" style="left:796px;top:150px" viewBox="0 0 120 70" aria-hidden="true"><path d="M0 70 L60 4 L120 70" fill="none" stroke="var(--ink)" stroke-width="4"/><circle cx="60" cy="6" r="6" fill="var(--ink)"/></svg>
  <div class="abs frame" style="left:716px;top:220px;width:280px;height:320px"><div class="picture" role="img" aria-label="Red car parked alone" style="background:linear-gradient(var(--sky) 60%,#c94a3f 60%)"></div></div>

  <div class="abs way" style="left:80px;top:580px;width:500px">
    <span class="abs way-num" style="left:0;top:0">1.</span>
    <p class="abs way-text" style="left:80px;top:4px;width:400px">Leaving your child to play outside by themselves, whether they are on your property or not.</p>
  </div>
  <div class="abs way" style="left:640px;top:580px;width:520px">
    <span class="abs way-num" style="left:0;top:0">2.</span>
    <p class="abs way-text" style="left:80px;top:4px;width:420px">Leaving your child in the car unsupervised, despite the length of time they are left alone.</p>
  </div>

  <svg class="abs hanger" style="left:256px;top:700px" viewBox="0 0 120 70" aria-hidden="true"><path d="M0 70 L60 4 L120 70" fill="none" stroke="var(--ink)" stroke-width="4"/><circle cx="60" cy="6" r="6" fill="var(--ink)"/></svg>
  <div class="abs frame" style="left:176px;top:770px;width:280px;height:300px"><div class="picture" role="img" aria-label="House standing alone" style="background:linear-gradient(var(--sky) 55%,#e3a048 55%)"></div></div>

  <svg class="abs hanger" style="left:796px;top:700px" viewBox="0 0 120 70" aria-hidden="true"><path d="M0 70 L60 4 L120 70" fill="none" stroke="var(--ink)" stroke-width="4"/><circle cx="60" cy="6" r="6" fill="var(--ink)"/></svg>
  <div class="abs frame" style="left:716px;top:770px;width:280px;height:300px"><div class="picture" role="img" aria-label="Two fists clashing" style="background:radial-gradient(circle,#f08a4b 30%,var(--sky) 70%)"></div></div>

  <div class="abs way" style="left:80px;top:1100px;width:500px">
    <span class="abs way-num" style="left:0;top:0">3.</span>
    <p class="abs way-text" style="left:80px;top:4px;width:400px">Leaving your child home alone without arranging for reasonable care or supervision.</p>
  </div>
  <div class="abs way" style="left:640px;top:1100px;width:520px">
    <span class="abs way-num" style="left:0;top:0">4.</span>
    <p class="abs way-text" style="left:80px;top:4px;width:420px">Becoming emotionally or physically combative with the other parent while your child is present.</p>
  </div>
</section>

</body>
</html>
```